New Business Card Design Project

We require a business card design for Vexalund, a newly established Indian company.
Our focus is on the development, manufacturing, and export of a diverse array of pharmaceutical products on a global scale. The card should convey a professional appearance, as our primary markets are in Africa, China, and Southeast Asian nations.
We envision a two-sided business card, with the reverse side dedicated to a logo set against a solid color or an elegantly designed pattern. The corners should be rounded. We would appreciate seeing both horizontal and vertical design options. We trust the designer to utilize their expertise in creating this design.

The content for the business card is included in the attached Word file.

Target Market(s)

Our primary markets are in Africa, China, and Southeast Asian, Latin America, Maldives, Sri Lanka

Industry/Entity Type

Pharmaceutical Manufacturing and Export

Contact Information for Business Card

Colors

Designer to choose colors to be used in the design.

Requirements
Must have
• The reverse side of the business card features solely the logo along with the tagline, "Wellness for All."
Should not have
• The logo should not exceed two instances, encompassing both the front and back sides of the card.

```html
<!DOCTYPE html>
<html lang="en">
<head>
<meta charset="utf-8">
<title>Vexalund Business Card</title>
<link rel="stylesheet" href="https://fonts.googleapis.com/css2?family=Montserrat:wght@400;800&family=Open+Sans:wght@400;700&display=swap">
<style>
  :root {
    --backdrop: #232323;
    --card: #1f1f22;
    --edge: #2ea7e0;
    --blue: #2ea7e0;
    --coral: #f0634f;
    --white: #f2f2f2;
    --ghost: #262a30;
  }
  * { margin: 0; padding: 0; box-sizing: border-box; }
  html, body {
    width: 1200px; height: 711px; overflow: hidden;
    background: var(--backdrop);
  }
  .canvas {
    position: relative; width: 1200px; height: 711px;
    display: flex; align-items: center; justify-content: center; gap: 40px;
  }
  .card {
    position: relative; width: 540px; height: 320px;
    background: var(--card);
    border-radius: 24px;
    border-bottom: 3px solid var(--edge);
    border-left: 2px solid var(--edge);
    box-shadow: 0 14px 30px rgba(0,0,0,.55);
    overflow: hidden;
  }
  /* Reverse side */
  .card--back {
    display: flex; flex-direction: column; align-items: center; justify-content: center;
  }
  .brand-mark { display: flex; align-items: center; gap: 14px; }
  .brand-dot { width: 22px; height: 22px; border-radius: 50%; background: var(--coral); flex: none; }
  .brand-name {
    font-family: 'Montserrat', sans-serif; font-weight: 800;
    color: var(--blue); font-size: 64px; letter-spacing: .5px; line-height: 1;
  }
  .tagline {
    margin-top: 16px;
    font-family: 'Montserrat', sans-serif; font-weight: 400;
    color: var(--white); font-size: 14px; letter-spacing: 1px;
  }
  /* Front side */
  .card--front .brand-name { font-size: 42px; }
  .card--front .brand-dot { width: 16px; height: 16px; }
  .front-brand { position: absolute; left: 34px; top: 42px; }
  .address {
    position: absolute; left: 36px; top: 112px;
    font-family: 'Open Sans', sans-serif; font-style: normal; font-size: 14px; line-height: 1.45;
    color: var(--white);
  }
  .contacts {
    position: absolute; left: 36px; bottom: 34px; list-style: none;
    font-family: 'Open Sans', sans-serif; font-size: 14px; color: var(--white);
  }
  .contacts li { display: flex; align-items: center; gap: 10px; line-height: 24px; }
  .contacts svg { width: 16px; height: 16px; flex: none; }
  .ghost-circle {
    position: absolute; right: 40px; top: 70px; width: 200px; height: 200px;
    border-radius: 50%; background: var(--ghost);
  }
  .person {
    position: absolute; right: 46px; top: 110px; text-align: right;
    font-family: 'Open Sans', sans-serif;
  }
  .person-name { font-size: 26px; line-height: 1.1; }
  .person-first { color: var(--blue); font-weight: 700; }
  .person-last { color: var(--coral); font-weight: 400; }
  .person-role { color: var(--white); font-size: 14px; margin-top: 4px; letter-spacing: 1px; }
  .accent-bar {
    position: absolute; right: 0; top: 108px; width: 18px; height: 56px; background: var(--blue);
  }
</style>
</head>
<body>
<main class="canvas">
  <section class="card card--back" aria-label="Card reverse side">
    <div class="brand-mark">
      <span class="brand-dot"></span>
      <span class="brand-name">Vexalund</span>
    </div>
    <p class="tagline">Wellness for All.</p>
  </section>

  <section class="card card--front" aria-label="Card front side">
    <div class="ghost-circle"></div>
    <div class="brand-mark front-brand">
      <span class="brand-dot"></span>
      <span class="brand-name">Vexalund</span>
    </div>
    <address class="address">
      12, Sunrise Colony,<br>Nashik, 422001, India
    </address>
    <ul class="contacts">
      <li>
        <svg viewBox="0 0 16 16" aria-hidden="true"><rect x="4" y="1" width="8" height="14" rx="1.5" fill="none" stroke="var(--coral)" stroke-width="1.6"/></svg>
        +91 90000 12345
      </li>
      <li>
        <svg viewBox="0 0 16 16" aria-hidden="true"><circle cx="8" cy="8" r="6.5" fill="none" stroke="var(--blue)" stroke-width="1.5"/><ellipse cx="8" cy="8" rx="3" ry="6.5" fill="none" stroke="var(--blue)" stroke-width="1.2"/><line x1="1.5" y1="8" x2="14.5" y2="8" stroke="var(--blue)" stroke-width="1.2"/></svg>
        www.vexalund.com
      </li>
      <li>
        <svg viewBox="0 0 16 16" aria-hidden="true"><rect x="1" y="3.5" width="14" height="10" rx="1" fill="none" stroke="var(--coral)" stroke-width="1.5"/><polyline points="1.5,4 8,9.5 14.5,4" fill="none" stroke="var(--coral)" stroke-width="1.5"/></svg>
        amalvade@vexalund.com
      </li>
    </ul>
    <div class="person">
      <p class="person-name"><span class="person-first">Arjun</span> <span class="person-last">K. Malvade</span></p>
      <p class="person-role">CEO</p>
    </div>
    <div class="accent-bar"></div>
  </section>
</main>
</body>
</html>
```